Construction company business card

One side to be the logo with the company name, The other side I would like: (Tomas verbick) Project manager 41 barrow crescent hallam 52917306224783(03) 9703 2428Info@gudeljgroup.comAnd then maybe a couple dot points saying what we do:Construction (commercial & industrial) Civil construction

Anything else please contact me!
Maybe curved st one edge of the card

Target Market(s)

Older clientele

Industry/Entity Type

Construction Company

Contact Information for Business Card

Read above

Colors
3277b5
1b1b1b
9d9d9d

Requirements
Must have
• Use my logo on one side
Nice to have
• Read above
Should not have
• Read above

```html
<!DOCTYPE html>
<html lang="en">
<head>
<meta charset="utf-8">
<title>Hallbrook Construction – Business Card</title>
<link rel="stylesheet" href="https://fonts.googleapis.com/css2?family=Work+Sans:wght@400;500;700&display=swap">
<style>
  :root {
    --blue: #1658a8;
    --ink: #1b1b1b;
    --grey: #9d9d9d;
    --charcoal: #4a4a4a;
    --slate: #555a60;
    --paper: #ffffff;
    --backdrop: #b9b9b9;
  }
  * { margin: 0; padding: 0; box-sizing: border-box; }
  html, body {
    width: 1200px; height: 930px; overflow: hidden;
    background: var(--backdrop);
    font-family: "Work Sans", sans-serif;
  }
  .stage { position: relative; width: 1200px; height: 930px; }

  .card {
    position: absolute;
    width: 560px; height: 320px;
    border-radius: 22px;
    overflow: hidden;
    box-shadow: 0 6px 18px rgba(0,0,0,.25);
  }

  /* Logo side */
  .card--logo {
    left: 70px; top: 110px;
    background: var(--charcoal);
    display: flex; align-items: center; justify-content: center;
  }
  .brand { display: flex; align-items: center; gap: 14px; }
  .brand__dot {
    width: 46px; height: 46px; border-radius: 50%;
    background: currentColor;
    flex: none;
  }
  .brand__name {
    font-weight: 700; letter-spacing: .04em; text-transform: uppercase;
    line-height: 1.1;
  }
  .card--logo .brand { color: var(--paper); }
  .card--logo .brand__name { font-size: 30px; }

  /* Details side */
  .card--details {
    left: 570px; top: 500px;
    background: var(--paper);
    color: var(--slate);
  }
  .card--details .brand {
    position: absolute; right: 36px; top: 34px;
    color: var(--blue);
  }
  .card--details .brand__dot { width: 34px; height: 34px; }
  .card--details .brand__name { font-size: 19px; }

  .rule {
    position: absolute; height: 1.5px; background: var(--blue);
  }
  .rule--top { left: 150px; right: 40px; top: 120px; }
  .rule--mid { left: 40px; width: 250px; top: 196px; }

  .person { position: absolute; left: 40px; top: 136px; }
  .person__name {
    color: var(--blue); font-weight: 500; font-size: 24px;
    text-transform: uppercase; letter-spacing: .01em;
  }
  .person__role { font-size: 16px; margin-top: 2px; }

  .contact {
    position: absolute; left: 40px; top: 210px;
    list-style: none; font-size: 15px; line-height: 22px;
  }
  .contact li { display: flex; align-items: center; gap: 8px; }
  .contact svg { width: 11px; height: 11px; fill: none; stroke: var(--blue); stroke-width: 2; }

  .address {
    position: absolute; right: 36px; top: 150px;
    text-align: right; font-size: 15px; line-height: 20px;
    font-style: normal;
  }

  .swoosh { position: absolute; left: 0; bottom: 0; width: 560px; height: 110px; }
</style>
</head>
<body>
<main class="stage">

  <section class="card card--logo" aria-label="Card front">
    <div class="brand">
      <span class="brand__dot"></span>
      <span class="brand__name">Hallbrook<br>Construction</span>
    </div>
  </section>

  <section class="card card--details" aria-label="Card back">
    <div class="brand">
      <span class="brand__dot"></span>
      <span class="brand__name">Hallbrook<br>Construction</span>
    </div>

    <div class="rule rule--top"></div>

    <div class="person">
      <h1 class="person__name">Tomas Verbick</h1>
      <p class="person__role">Project manager</p>
    </div>

    <div class="rule rule--mid"></div>

    <ul class="contact">
      <li><svg viewBox="0 0 12 12"><path d="M3 1 L5 4 L4 5 Q5 7 7 8 L8 7 L11 9 L10 11 Q4 11 1 3 Z"/></svg>73 0622 4783</li>
      <li><svg viewBox="0 0 12 12"><rect x="3" y="1" width="6" height="10" rx="1"/></svg>03 9418 6573</li>
      <li><svg viewBox="0 0 12 12"><rect x="1" y="2.5" width="10" height="7"/><path d="M1 3 L6 7 L11 3"/></svg>Info@verbickgroup.com</li>
    </ul>

    <address class="address">41 barrow<br>crescent dunmore 5291</address>

    <svg class="swoosh" viewBox="0 0 560 110" preserveAspectRatio="none" aria-hidden="true">
      <path d="M0 98 L370 78 Q395 76 410 58 Q430 34 460 32 L560 26 L560 110 L0 110 Z" fill="var(--blue)"/>
      <path d="M0 92 L360 70 Q380 68 392 56" stroke="var(--slate)" stroke-width="5" fill="none"/>
    </svg>
  </section>

</main>
</body>
</html>
```